Investment Management Firm Power point template

Marrow Holdings is a real estate investment firm focused on buying commercial office and residential property in the UK. We produce powerpoint presentations for our Board of Directors, Investment Committee and also to external investors.

We are looking for a powerpoint design template which we can use for future presentations which provide a professional look and feel.

Our current website: http://www.marrowholdings.example.co.uk/

Target Market(s)

Institution Investors, Board of Directors, Professionals

Industry/Entity Type

Real Estate

Requirements
Must have
• Leverage off the current logo and colour scheme. However, does not have to purely rely on this colour scheme.
• - Title page
• - Content Page
• - Slide where graphs can be incorporated
• - Slide where photos can be incorporated
• - Slide of UK Map which can show where the property portfolio is currently located
• - Other slides incorporating smart art or other designs that can be used for future presentations
Nice to have
• An example of graphics that we would love to have in the powerpoint pack which we can easily edit has been attached

```html
<!DOCTYPE html>
<html lang="en">
<head>
<meta charset="utf-8">
<title>About Us – Marrow Holdings</title>
<link href="https://fonts.googleapis.com/css2?family=Titillium+Web:wght@300;400;700&display=swap" rel="stylesheet">
<style>
  :root {
    --navy: #0b3c6c;
    --photo-light: #3573aa;
    --photo-mid: #21588c;
    --photo-dark: #123f6c;
    --panel-fill: rgba(10, 55, 100, 0.72);
    --panel-line: #4a9fe2;
    --text: #ffffff;
    --brand-line: #9fb8d2;
  }
  * { margin: 0; padding: 0; box-sizing: border-box; }
  html, body { width: 1200px; height: 900px; overflow: hidden; background: var(--navy); }
  .slide {
    position: relative;
    width: 1200px;
    height: 900px;
    background: var(--navy);
    font-family: "Titillium Web", sans-serif;
    color: var(--text);
    overflow: hidden;
  }
  .hero-image {
    position: absolute;
    left: 558px;
    top: 0;
    width: 642px;
    height: 900px;
    background:
      linear-gradient(160deg, var(--photo-light) 0%, var(--photo-mid) 45%, var(--photo-dark) 100%);
  }
  .slide-title {
    position: absolute;
    left: 49px;
    top: 26px;
    font-size: 40px;
    font-weight: 700;
    letter-spacing: 0.2px;
  }
  .about-panel {
    position: absolute;
    left: 98px;
    top: 246px;
    width: 971px;
    height: 440px;
    background: var(--panel-fill);
    border: 1.5px solid var(--panel-line);
    display: flex;
    flex-direction: column;
    justify-content: center;
    padding: 0 40px;
    text-align: center;
  }
  .about-panel p {
    font-size: 20.5px;
    font-weight: 300;
    line-height: 36px;
  }
  .about-panel p + p { margin-top: 37px; }
  .brand {
    position: absolute;
    left: 15px;
    top: 845px;
    width: 226px;
    height: 39px;
    border: 1px solid var(--brand-line);
    display: flex;
    align-items: center;
    gap: 12px;
    padding-left: 8px;
  }
  .brand-mark {
    width: 26px;
    height: 26px;
    border: 1.5px solid var(--text);
  }
  .brand-name {
    font-size: 22px;
    font-weight: 400;
    color: var(--text);
    white-space: nowrap;
  }
</style>
</head>
<body>
  <div class="slide">
    <div class="hero-image" role="img" aria-label="Blue-tinted photograph of modern glass office towers viewed from below"></div>

    <h1 class="slide-title">About Us</h1>

    <section class="about-panel">
      <p>While a property’s fundamentals are important to us, we put equal focus on the people who use and enjoy our spaces. The experience of being in our buildings — from design to atmosphere — is strategically planned. Functionality and efficiency are crucial and technology is in our DNA.</p>
      <p>With these fundamental characteristics in mind we strive to create businesses around our properties, enhancing their value and creating long-term operating platforms.</p>
      <p>As part of the Ashcombe Reach Group we directly and indirectly benefit from the ecosystem of companies around us. Ashcombe Reach brings unrivalled expertise in building successful, long-lasting businesses.</p>
    </section>

    <div class="brand">
      <span class="brand-mark"></span>
      <span class="brand-name">Marrow Holdings</span>
    </div>
  </div>
</body>
</html>
```